New, modern business card for growing audiology practice

We need a new business card for our audiology practice. Our logo and website have recently changed (more modern) and we want our business cards to reflect this change.
We conduct hearing tests, perform earwax removals, and fit & dispense hearing aids to our patients. We are a family owned practice in which the owner is the one who works directly with the patient. I have attached logos in various formats to use, as well as two ideas I found on this website; as well as a scanned copy of our current logo. Good luck!

Industry/Entity Type

Business

Contact Information for Business Card

Company name: Tolvera Hearing Center
Provider name: Peter Wolstenby, Au.D. F/NSB
Phone number: (440) 683-5127
Address: 837 W. Lindell Ave. Ashbury Glen, OH 44391
email: tolverahearing@postvane.com
website: tolverahearing.com

Colors
000000
aaaaaa
dbdbdb
cacaca
9bcb3c
afd23c
cadf82
b1b1b1

Requirements
Must have
• My card must include information in the "details" section. In the attached images, I found a few that I liked and I would like to model after - "brisky bouncin'" and "Sound Method Center".
• Must be horizontal.
• Must include logos provided. I uploaded them in various file formats and various ways.
• Must match logo font, if possible, if not, please get as close as you can.
Nice to have
• I really like the idea of having a color on one side with just the logo and company name and the contact information and provider name on the other side. I also really like the idea of having the main color dominating on the logo/company side with accent of that same color on the contact side of the card.
Should not have
• Must not be vertical.

```html
<!DOCTYPE html>
<html lang="en">
<head>
<meta charset="utf-8">
<title>Tolvera Hearing Center – Business Card</title>
<link href="https://fonts.googleapis.com/css2?family=Lato:wght@300;400;700&display=swap" rel="stylesheet">
<style>
  :root {
    --stage: #141514;
    --card-top: #2b2d2b;
    --card-bottom: #181918;
    --green: #9bcb3c;
    --green-soft: #afd23c;
    --white: #f2f2f2;
    --grey: #b1b1b1;
  }
  * { margin: 0; padding: 0; box-sizing: border-box; }
  html, body {
    width: 1200px; height: 1031px; overflow: hidden;
    background: var(--stage);
    font-family: "Lato", sans-serif;
  }
  .sheet {
    width: 1200px; height: 1031px;
    display: flex; flex-direction: column; align-items: center; justify-content: center;
    gap: 70px;
  }
  .card {
    position: relative;
    width: 700px; height: 400px;
    border-radius: 24px;
    background: linear-gradient(160deg, var(--card-top), var(--card-bottom));
    box-shadow: 0 10px 30px rgba(0,0,0,.6);
    overflow: hidden;
  }

  /* Front */
  .card--front { display: flex; flex-direction: column; justify-content: center; padding-left: 90px; }
  .brand { display: flex; align-items: center; gap: 18px; }
  .brand__dot {
    width: 40px; height: 40px; border-radius: 50%;
    border: 6px solid var(--green);
    flex: none;
  }
  .brand__name {
    color: var(--white); font-weight: 400; font-size: 36px;
    letter-spacing: 1px; text-transform: uppercase;
  }
  .address {
    margin-top: 34px; margin-left: 58px;
    display: flex; align-items: center; gap: 10px;
    color: var(--white); font-size: 18px; font-weight: 400;
  }
  .address svg { width: 14px; height: 18px; flex: none; }

  /* Back */
  .card--back { display: flex; }
  .back__mark {
    width: 300px; display: flex; flex-direction: column; align-items: center; justify-content: center; gap: 18px;
  }
  .back__circle {
    width: 130px; height: 130px; border-radius: 50%;
    border: 16px solid var(--green);
  }
  .back__name {
    color: var(--green); font-size: 17px; font-weight: 400;
    text-transform: uppercase; letter-spacing: 1px;
  }
  .back__details { flex: 1; padding: 70px 40px 0 20px; }
  .person__name {
    color: var(--green); font-size: 30px; font-weight: 400;
    text-transform: uppercase; letter-spacing: .5px;
  }
  .person__title { color: var(--white); font-size: 24px; font-weight: 400; margin-top: 2px; }
  .divider {
    height: 2px; width: 300px; margin: 26px 0 24px;
    background: linear-gradient(90deg, var(--green), rgba(155,203,60,0));
  }
  .contact { list-style: none; }
  .contact li {
    display: flex; align-items: center; gap: 12px;
    color: var(--white); font-size: 18px; line-height: 32px;
  }
  .contact svg { width: 18px; height: 18px; flex: none; }
</style>
</head>
<body>
<main class="sheet">

  <section class="card card--front" aria-label="Card front">
    <div class="brand">
      <span class="brand__dot"></span>
      <h1 class="brand__name">Tolvera Hearing Center</h1>
    </div>
    <p class="address">
      <svg viewBox="0 0 14 18" aria-hidden="true"><path d="M7 0a7 7 0 0 0-7 7c0 5 7 11 7 11s7-6 7-11a7 7 0 0 0-7-7zm0 9.5A2.5 2.5 0 1 1 7 4.5a2.5 2.5 0 0 1 0 5z" fill="var(--green)"/></svg>
      837 W. Lindell Ave. Ashbury Glen, OH 44391
    </p>
  </section>

  <section class="card card--back" aria-label="Card back">
    <div class="back__mark">
      <span class="back__circle"></span>
      <span class="back__name">Tolvera Hearing Center</span>
    </div>
    <div class="back__details">
      <h2 class="person__name">Peter Wolstenby</h2>
      <p class="person__title">Au.D. F/NSB</p>
      <div class="divider"></div>
      <ul class="contact">
        <li>
          <svg viewBox="0 0 18 18" aria-hidden="true"><circle cx="9" cy="9" r="9" fill="var(--green)"/><path d="M6 4.5l1.6 2.4-1 1c.6 1.3 1.6 2.3 2.9 2.9l1-1 2.4 1.6-1 1.6C9 13 5 9 4.4 5.5z" fill="var(--card-bottom)"/></svg>
          (440) 683-5127
        </li>
        <li>
          <svg viewBox="0 0 18 18" aria-hidden="true"><rect x="1" y="3.5" width="16" height="11" rx="1.5" fill="var(--green)"/><path d="M1.5 4.5L9 10l7.5-5.5" stroke="var(--card-bottom)" stroke-width="1.4" fill="none"/></svg>
          tolverahearing@postvane.com
        </li>
        <li>
          <svg viewBox="0 0 18 18" aria-hidden="true"><circle cx="9" cy="9" r="8" fill="var(--green)"/><path d="M1 9h16M9 1c-3 3-3 13 0 16M9 1c3 3 3 13 0 16" stroke="var(--card-bottom)" stroke-width="1.2" fill="none"/></svg>
          www.tolverahearing.com
        </li>
      </ul>
    </div>
  </section>

</main>
</body>
</html>
```